Brandwyn Fuel Retro Website Design

Have a logo. Need a website design to go along with the logo design. Full Design Specs are here: https://files.plinverdocs.net/sheet/d/8QmRtZxWv3-41pk527LNB_XY4HaPcOdsuw2K-rb6/view

Target Market(s)

Independent Gas Station Owners

Number of Pages Required

1 page

Font styles to use
Sans Serif

Colors

Designer to choose colors to be used in the design.

```html
<!DOCTYPE html>
<html lang="en">
<head>
<meta charset="utf-8">
<title>Brandwyn Fuel – Home</title>
<link href="https://fonts.googleapis.com/css2?family=Lato:wght@300;400;700;900&family=Archivo+Black&family=Bangers&display=swap" rel="stylesheet">
<style>
:root{
  --red:#e8262e;
  --red-dark:#c81a22;
  --ink:#4a4a4a;
  --text:#555555;
  --paper:#f7f7f7;
  --line:#c9c9c9;
  --slate:#57595c;
}
*{box-sizing:border-box;margin:0;padding:0}
html,body{width:932px;height:1200px;overflow:hidden;background:#ffffff}
.stage{position:absolute;left:3px;top:0;width:1690px;height:2190px;transform:scale(0.548);transform-origin:0 0}
.page{position:absolute;top:2px;width:634px;height:2178px;background:var(--paper);border:1px solid var(--line);font-family:"Lato",sans-serif;color:var(--text)}
.page--a{left:116px}
.page--b{left:916px}
.abs{position:absolute}
.brand{left:22px;top:30px;display:flex;align-items:center;gap:9px}
.brand__dot{width:40px;height:40px;border-radius:50%;background:var(--red)}
.brand__name{font-family:"Lato",sans-serif;font-weight:900;font-size:16px;color:var(--ink);letter-spacing:.2px}
.since{left:450px;top:28px;width:185px;text-align:center;font-family:"Bangers",sans-serif;color:var(--red);font-size:31px;letter-spacing:.5px}
.phone{left:450px;top:63px;width:185px;text-align:center;font-family:"Bangers",sans-serif;color:var(--red);font-size:17px;letter-spacing:.3px}
.nav{left:11px;top:102px;width:613px;height:41px;background:var(--red);border-radius:3px;display:flex;align-items:center;padding-left:11px;font-size:9.5px;font-weight:700;color:#fff;letter-spacing:.2px}
.nav__item{padding:6px 8px;border-radius:3px;margin-right:12px;white-space:nowrap}
.nav__item--home{background:var(--red-dark)}
.nav__item--active{background:var(--slate)}
.photo{position:absolute;border-radius:2px;box-shadow:0 1px 2px rgba(0,0,0,.18)}
.photo--building{left:11px;top:155px;width:613px;height:291px;background:
  linear-gradient(180deg,rgba(0,0,0,0) 55%,rgba(40,38,36,.55) 100%),
  linear-gradient(180deg,#7d8288 0%,#9da1a4 30%,#c9c6c0 48%,#a23a36 50%,#d8d4cc 52%,#8e8a84 78%,#4f4d4b 100%)}
.hero__circle{left:64px;top:198px;width:172px;height:172px;border-radius:50%;background:rgba(70,70,72,.72)}
.hero__ribbon{left:35px;top:222px}
.hero__title{left:35px;top:226px;width:225px;text-align:center;font-family:"Archivo Black",sans-serif;color:#fff;font-size:23px;line-height:34px}
.hero__text{left:70px;top:274px;width:160px;text-align:center;color:#fff;font-size:8.5px;line-height:14px}
.btn{position:absolute;width:69px;height:23px;background:var(--red);color:#fff;font-family:"Lato",sans-serif;font-size:9.5px;display:flex;align-items:center;justify-content:center;border-radius:2px}
.btn--pill{border-radius:12px;width:83px;height:21px}
.label{position:absolute;background:var(--slate);color:#fff;font-weight:700;font-size:11px;display:flex;align-items:center;justify-content:center;border-radius:2px;height:34px;white-space:nowrap}
.copy{position:absolute;font-weight:400;font-size:9px;line-height:19.6px;color:var(--text);white-space:nowrap}
.copy--tight{line-height:16.4px}
.copy--wrap{white-space:normal}
.carousel{left:11px;top:1072px;width:613px;height:202px;background:
  radial-gradient(ellipse at 50% 30%,rgba(120,110,98,.55),rgba(0,0,0,0) 65%),
  linear-gradient(90deg,#2f2b28,#4d4741 50%,#302c29)}
.thumb{position:absolute;box-shadow:0 2px 6px rgba(0,0,0,.45);background:
  linear-gradient(180deg,#a08866 0%,#7a6a58 35%,#5a5f78 55%,#9a5a4c 80%,#6a5a50 100%)}
.chev{position:absolute}
.section-title{position:absolute;left:263px;top:1327px;width:310px;text-align:center;font-weight:700;font-size:10.5px;color:#3a3a3a}
.footer{left:10px;top:2071px;width:615px;height:95px;background:var(--ink);border-top:3px solid var(--red)}
.footer__brand{left:38px;top:30px;display:flex;align-items:center;gap:6px}
.footer__dot{width:26px;height:26px;border-radius:50%;background:var(--red)}
.footer__name{font-weight:900;font-size:10.5px;color:#fff}
.footer__copy{left:28px;top:76px;font-size:7.5px;color:#fff}
.ph-truck{background:linear-gradient(180deg,#cdd5d8 0%,#b8c0c2 50%,#8d9090 62%,#e6e6e4 66%,#d2d2d0 80%,#6e6f6c 100%)}
.ph-oils{background:linear-gradient(135deg,#9a7448 0%,#c9a46a 20%,#c83a40 45%,#e8e2dc 62%,#2c2a34 80%,#4a3a6a 100%)}
.ph-tank-grey{background:linear-gradient(180deg,#6d675e 0%,#8f9396 25%,#a6a9ab 55%,#858380 80%,#8c8a86 100%)}
.ph-tank-white{background:linear-gradient(180deg,#7a7670 0%,#8a8680 20%,#ededeb 45%,#d6d5d2 75%,#a9a6a0 100%)}
.ph-tank-trees{background:linear-gradient(180deg,#b0b4b8 0%,#6d6a66 45%,#e8e8e6 65%,#c9c8c4 85%,#8f8c86 100%)}
.ph-container-doors{background:linear-gradient(90deg,#7a7e83 0%,#8e9297 50%,#6f7378 100%)}
.ph-container-field{background:linear-gradient(180deg,#cfd3d5 0%,#b9bdc0 30%,#7e8286 45%,#70757a 70%,#6f7a5e 85%,#5e6a4c 100%)}
</style>
</head>
<body>
<div class="stage">

<main class="page page--a">
  <header>
    <div class="abs brand"><span class="brand__dot"></span><span class="brand__name">Brandwyn Fuel</span></div>
    <div class="abs since">SINCE 1996</div>
    <div class="abs phone">PHONE : 5550142283</div>
    <nav class="abs nav">
      <span class="nav__item nav__item--home">HOME</span>
      <span class="nav__item nav__item--active">FUEL DELIEVERY</span>
      <span class="nav__item">OIL</span>
      <span class="nav__item">FARM FUEL</span>
      <span class="nav__item">CARGO CONTAINERS</span>
    </nav>
  </header>

  <section class="hero">
    <div class="photo photo--building" role="img" aria-label="Photo of the fuel company storefront with trucks parked outside"></div>
    <div class="abs hero__circle"></div>
    <svg class="abs hero__ribbon" width="226" height="44" viewBox="0 0 226 44"><polygon points="0,0 226,0 212,22 226,44 0,44 14,22" fill="#e8262e"/></svg>
    <div class="abs hero__title">WE ARE HERE</div>
    <p class="abs hero__text">Fuel Delivery , Oil delivery. Brandwyn Fuel has been around since 1966</p>
    <span class="btn btn--pill" style="left:107px;top:307px">More</span>
  </section>

  <section class="service">
    <div class="photo ph-truck" style="left:10px;top:482px;width:288px;height:259px" role="img" aria-label="Photo of a white fuel delivery truck"></div>
    <div class="label" style="left:246px;top:503px;width:104px">FUEL DELIVERY</div>
    <p class="copy" style="left:350px;top:564px">Brandwyn Fuel provides fuel delivery for independent gas sta-<br>tions, convenience stores, construction sites or any other<br>commercial need. If you are looking for gasoline, high<br>sulfer diesel fuel, farm diesel or other bulk fuel delivered to<br>your business, we will take care of you!</p>
    <span class="btn" style="left:351px;top:680px">More</span>
  </section>

  <section class="service">
    <div class="photo ph-oils" style="left:335px;top:776px;width:287px;height:259px" role="img" aria-label="Photo of motor oil jugs and shop shelves"></div>
    <div class="label" style="left:303px;top:807px;width:59px">OILS</div>
    <p class="copy" style="left:32px;top:860px">Looking for speciality auto, tractor, tractor trailer, aviation<br>or other commercial oils and lubricants Brandwyn Fuel can<br>help! Just call one of our customer oriented staff and we<br>will get what you need quick! We have a complete line of<br>aviation oils and lubricants as well as gear lubricants,<br>greases, oils and more!</p>
    <span class="btn" style="left:32px;top:995px">More</span>
  </section>

  <section class="abs carousel">
    <div class="thumb" style="left:60px;top:48px;width:127px;height:97px" role="img" aria-label="Photo of stocked shop shelves"></div>
    <div class="thumb" style="left:231px;top:36px;width:160px;height:120px" role="img" aria-label="Photo of oil products on shelving"></div>
    <div class="thumb" style="left:434px;top:48px;width:127px;height:97px" role="img" aria-label="Photo of lubricant display"></div>
    <svg class="chev" style="left:8px;top:82px" width="24" height="34" viewBox="0 0 24 34"><polyline points="20,2 4,17 20,32" fill="none" stroke="#fff" stroke-width="2.5"/></svg>
    <svg class="chev" style="left:582px;top:82px" width="24" height="34" viewBox="0 0 24 34"><polyline points="4,2 20,17 4,32" fill="none" stroke="#fff" stroke-width="2.5"/></svg>
  </section>

  <section class="service">
    <div class="photo ph-tank-grey" style="left:10px;top:1310px;width:201px;height:173px" role="img" aria-label="Photo of a grey farm fuel tank"></div>
    <h2 class="section-title">FARM FUEL</h2>
    <p class="copy copy--tight copy--wrap" style="left:263px;top:1355px;width:310px;text-align:center">Looking for gasoline, diesel red diesel off road fuel or farm diesel? We can deliver straight to your farm! We can setup your farm tanks, take care of EPA containment and deliver fuel when you need it!</p>
    <span class="btn" style="left:386px;top:1418px">More</span>
    <div class="abs" style="left:10px;top:1486px;width:613px;height:2px;background:var(--red)"></div>
    <div class="photo ph-tank-white" style="left:10px;top:1489px;width:201px;height:173px" role="img" aria-label="Photo of two white fuel tanks"></div>
    <div class="photo ph-tank-white" style="left:216px;top:1489px;width:201px;height:173px" role="img" aria-label="Photo of a white horizontal fuel tank"></div>
    <div class="photo ph-tank-trees" style="left:422px;top:1489px;width:201px;height:173px" role="img" aria-label="Photo of a white tank beside bare trees"></div>
  </section>

  <section class="service">
    <div class="photo ph-container-doors" style="left:29px;top:1706px;width:230px;height:210px" role="img" aria-label="Photo of grey cargo container doors"></div>
    <div class="photo ph-container-field" style="left:171px;top:1865px;width:201px;height:163px" role="img" aria-label="Photo of a grey cargo container on grass"></div>
    <div class="label" style="left:205px;top:1722px;width:119px">CARGO CONTAINERS</div>
    <p class="copy copy--tight" style="left:302px;top:1764px">Want to purchase or lease a storage container, we have what you<br>need! We can deliver or move storage containers to your home,<br>business, construction site or any you need one!</p>
    <span class="btn" style="left:302px;top:1822px">More</span>
  </section>

  <footer class="abs footer">
    <div class="abs footer__brand"><span class="footer__dot"></span><span class="footer__name">Brandwyn Fuel</span></div>
    <p class="abs footer__copy">© 2019brandwynfuel.com</p>
  </footer>
</main>

<main class="page page--b">
  <header>
    <div class="abs brand"><span class="brand__dot"></span><span class="brand__name">Brandwyn Fuel</span></div>
    <div class="abs since">SINCE 1996</div>
    <div class="abs phone">PHONE : 5550142283</div>
    <nav class="abs nav">
      <span class="nav__item nav__item--home">HOME</span>
      <span class="nav__item nav__item--active">FUEL DELIEVERY</span>
      <span class="nav__item">OIL</span>
      <span class="nav__item">FARM FUEL</span>
      <span class="nav__item">CARGO CONTAINERS</span>
    </nav>
  </header>

  <section class="hero">
    <div class="photo photo--building" role="img" aria-label="Photo of the fuel company storefront with trucks parked outside"></div>
    <div class="abs hero__circle"></div>
    <svg class="abs hero__ribbon" width="226" height="44" viewBox="0 0 226 44"><polygon points="0,0 226,0 212,22 226,44 0,44 14,22" fill="#e8262e"/></svg>
    <div class="abs hero__title">WE ARE HERE</div>
    <p class="abs hero__text">Fuel Delivery , Oil delivery. Brandwyn Fuel has been around since 1966</p>
    <span class="btn btn--pill" style="left:107px;top:307px">More</span>
  </section>

  <section class="service">
    <div class="photo ph-truck" style="left:10px;top:482px;width:288px;height:259px" role="img" aria-label="Photo of a white fuel delivery truck"></div>
    <div class="label" style="left:246px;top:503px;width:104px">FUEL DELIVERY</div>
    <p class="copy" style="left:350px;top:564px">Brandwyn Fuel provides fuel delivery for independent gas sta-<br>tions, convenience stores, construction sites or any other<br>commercial need. If you are looking for gasoline, high<br>sulfer diesel fuel, farm diesel or other bulk fuel delivered to<br>your business, we will take care of you!</p>
    <span class="btn" style="left:351px;top:680px">More</span>
  </section>

  <section class="service">
    <div class="photo ph-oils" style="left:335px;top:776px;width:287px;height:259px" role="img" aria-label="Photo of motor oil jugs and shop shelves"></div>
    <div class="label" style="left:303px;top:807px;width:59px">OILS</div>
    <p class="copy" style="left:32px;top:860px">Looking for speciality auto, tractor, tractor trailer, aviation<br>or other commercial oils and lubricants Brandwyn Fuel can<br>help! Just call one of our customer oriented staff and we<br>will get what you need quick! We have a complete line of<br>aviation oils and lubricants as well as gear lubricants,<br>greases, oils and more!</p>
    <span class="btn" style="left:32px;top:995px">More</span>
  </section>

  <section class="abs carousel">
    <div class="thumb" style="left:60px;top:48px;width:127px;height:97px" role="img" aria-label="Photo of stocked shop shelves"></div>
    <div class="thumb" style="left:231px;top:36px;width:160px;height:120px" role="img" aria-label="Photo of oil products on shelving"></div>
    <div class="thumb" style="left:434px;top:48px;width:127px;height:97px" role="img" aria-label="Photo of lubricant display"></div>
    <svg class="chev" style="left:8px;top:82px" width="24" height="34" viewBox="0 0 24 34"><polyline points="20,2 4,17 20,32" fill="none" stroke="#fff" stroke-width="2.5"/></svg>
    <svg class="chev" style="left:582px;top:82px" width="24" height="34" viewBox="0 0 24 34"><polyline points="4,2 20,17 4,32" fill="none" stroke="#fff" stroke-width="2.5"/></svg>
  </section>

  <section class="service">
    <div class="photo ph-tank-grey" style="left:10px;top:1310px;width:201px;height:173px" role="img" aria-label="Photo of a grey farm fuel tank"></div>
    <h2 class="section-title">FARM FUEL</h2>
    <p class="copy copy--tight copy--wrap" style="left:263px;top:1355px;width:310px;text-align:center">Looking for gasoline, diesel red diesel off road fuel or farm diesel? We can deliver straight to your farm! We can setup your farm tanks, take care of EPA containment and deliver fuel when you need it!</p>
    <span class="btn" style="left:386px;top:1418px">More</span>
    <div class="abs" style="left:10px;top:1486px;width:613px;height:2px;background:var(--red)"></div>
    <div class="photo ph-tank-white" style="left:10px;top:1489px;width:201px;height:173px" role="img" aria-label="Photo of two white fuel tanks"></div>
    <div class="photo ph-tank-white" style="left:216px;top:1489px;width:201px;height:173px" role="img" aria-label="Photo of a white horizontal fuel tank"></div>
    <div class="photo ph-tank-trees" style="left:422px;top:1489px;width:201px;height:173px" role="img" aria-label="Photo of a white tank beside bare trees"></div>
  </section>

  <section class="service">
    <div class="photo ph-container-doors" style="left:29px;top:1706px;width:230px;height:210px" role="img" aria-label="Photo of grey cargo container doors"></div>
    <div class="photo ph-container-field" style="left:171px;top:1865px;width:201px;height:163px" role="img" aria-label="Photo of a grey cargo container on grass"></div>
    <div class="label" style="left:205px;top:1722px;width:119px">CARGO CONTAINERS</div>
    <p class="copy copy--tight" style="left:302px;top:1764px">Want to purchase or lease a storage container, we have what you<br>need! We can deliver or move storage containers to your home,<br>business, construction site or any you need one!</p>
    <span class="btn" style="left:302px;top:1822px">More</span>
  </section>

  <footer class="abs footer">
    <div class="abs footer__brand"><span class="footer__dot"></span><span class="footer__name">Brandwyn Fuel</span></div>
    <p class="abs footer__copy">© 2019brandwynfuel.com</p>
  </footer>
</main>

</div>
</body>
</html>
```